Brightmill Data Works

Our company is about IT hardwares and IT solutions. IT hardware such as PC, RAMS, storage and servers. IT solutions such as project management, BA. We are also selling new technology too.

Target Market(s)

Consumer, Small to Medium Business, Corporate

Requirements
Must have
• The business card must have the following:
• Name:
• Title:
• Contact Number:
• Email address:
• Website:
• Color: Must match the logo color upgrade

```html
<!DOCTYPE html>
<html lang="en">
<head>
<meta charset="utf-8">
<title>Brightmill Data Works – Business Card</title>
<link href="https://fonts.googleapis.com/css2?family=Lato:wght@400;700&family=Saira+Semi+Condensed:wght@700&display=swap" rel="stylesheet">
<style>
  :root {
    --stage: #1b1b1b;
    --card-light: #f3f3f3;
    --card-dark: #4a4a4a;
    --ink: #3f3f3f;
    --accent: #d4832f;
    --accent-deep: #c46a28;
    --white: #ffffff;
  }
  html, body {
    margin: 0;
    padding: 0;
    width: 1200px;
    height: 900px;
    overflow: hidden;
    background: var(--stage);
  }
  .canvas {
    position: relative;
    width: 1200px;
    height: 900px;
    background: var(--stage);
    font-family: "Lato", Arial, sans-serif;
  }
  .card {
    position: absolute;
    top: 200px;
    width: 310px;
    height: 502px;
    box-shadow: 0 3px 6px rgba(0,0,0,0.45);
  }
  .card-front {
    left: 253px;
    background: var(--card-light);
    border-radius: 62px 0 62px 0;
  }
  .card-back {
    left: 627px;
    width: 309px;
    background: var(--card-dark);
    border-radius: 0 62px 0 62px;
  }
  .brand-mark {
    position: absolute;
    left: 144px;
    top: 98px;
    width: 22px;
    height: 22px;
    background: var(--accent);
  }
  .brand-name {
    position: absolute;
    left: 0;
    top: 160px;
    width: 100%;
    text-align: center;
    font-family: "Saira Semi Condensed", "Arial Narrow", sans-serif;
    font-weight: 700;
    font-size: 37px;
    line-height: 38px;
    color: var(--ink);
    letter-spacing: 0.5px;
    margin: 0;
  }
  .holder {
    position: absolute;
    left: 34px;
    top: 317px;
  }
  .holder-name {
    margin: 0;
    font-weight: 700;
    font-size: 18px;
    color: var(--ink);
    letter-spacing: 0.2px;
    padding-left: 1px;
  }
  .holder-title {
    margin: 3px 0 0;
    font-size: 14.5px;
    color: var(--accent-deep);
  }
  .contacts {
    position: absolute;
    left: 33px;
    top: 387px;
    margin: 0;
    padding: 0;
    list-style: none;
  }
  .contacts li {
    display: flex;
    align-items: center;
    height: 24.5px;
    font-size: 15px;
    color: var(--ink);
  }
  .contact-icon {
    width: 19px;
    height: 19px;
    margin-right: 5px;
    flex: none;
  }
  .back-name {
    position: absolute;
    left: 0;
    top: 218px;
    width: 100%;
    text-align: center;
    margin: 0;
    font-family: "Saira Semi Condensed", "Arial Narrow", sans-serif;
    font-weight: 700;
    font-size: 40px;
    line-height: 42px;
    color: var(--accent);
  }
  .back-web {
    position: absolute;
    left: 0;
    top: 439px;
    width: 100%;
    text-align: center;
    margin: 0;
    font-size: 13.5px;
    font-weight: 700;
    letter-spacing: 0.6px;
    color: var(--white);
  }
</style>
</head>
<body>
<main class="canvas">
  <section class="card card-front" aria-label="Business card front">
    <div class="brand-mark" aria-hidden="true"></div>
    <h1 class="brand-name">BRIGHTMILL<br>DATA WORKS</h1>
    <div class="holder">
      <p class="holder-name">DANIEL HARLOW</p>
      <p class="holder-title">MANAGING DIRECTOR</p>
    </div>
    <ul class="contacts">
      <li>
        <svg class="contact-icon" viewBox="0 0 20 20" aria-hidden="true">
          <circle cx="10" cy="10" r="10" fill="var(--accent-deep)"/>
          <path d="M5.5 8.5c0-2 2-3 4.5-3s4.5 1 4.5 3l-2 .5-.5-1.5h-4l-.5 1.5z" fill="#fff"/>
          <rect x="6.5" y="10" width="7" height="4.5" rx="1" fill="#fff"/>
        </svg>
        044-987 650 312
      </li>
      <li>
        <svg class="contact-icon" viewBox="0 0 20 20" aria-hidden="true">
          <circle cx="10" cy="10" r="10" fill="var(--accent-deep)"/>
          <rect x="5" y="6.5" width="10" height="7" rx="0.8" fill="#fff"/>
          <path d="M5.3 7l4.7 3.6L14.7 7" fill="none" stroke="var(--accent-deep)" stroke-width="1"/>
        </svg>
        INFO@BRIGHTMILL.COM
      </li>
      <li>
        <svg class="contact-icon" viewBox="0 0 20 20" aria-hidden="true">
          <circle cx="10" cy="10" r="10" fill="var(--accent-deep)"/>
          <circle cx="10" cy="10" r="4.8" fill="#fff"/>
          <path d="M7.5 8.2l2 .6.8 1.8-1 1.6M11.5 6.2l.4 1.6 1.6.4" fill="none" stroke="var(--accent-deep)" stroke-width="1"/>
        </svg>
        WWW.BRIGHTMILLDATA.COM
      </li>
    </ul>
  </section>

  <section class="card card-back" aria-label="Business card back">
    <p class="back-name">BRIGHTMILL<br>DATA WORKS</p>
    <p class="back-web">www.brightmilldata.com</p>
  </section>
</main>
</body>
</html>
```